Website to design and sell sundials: www.gnomonvale.com

We have a website that creates a free paper sundial, we want to migrate from this not profit free website to a website where we will continue offering the free paper sundial model but We will also offer a manufactured sundial and sell it.
In order to understand the project, please visit:
http://www.gnomonvale.com/vertical/sundial.html and
http://www.torvel.net/landing/

The website user journey should be redesigned, including the phases that are,
select language
Show product give info
Creation/edit sundial (could be one or more phases)
View created sundial
Buy sundial.

May some of them could be combined or splitted, what It have more sense.

Requirements
Must have
• A description page user journey offering freemium paper sundial and physical sundial to sell.
• A sundial creation page for "free" paper sundial
• A result page for paper sundial
• A sell page for physical

```html
<!DOCTYPE html>
<html lang="en">
<head>
<meta charset="utf-8">
<title>GnomonVale — Sundials</title>
<link href="https://fonts.googleapis.com/css2?family=Open+Sans:wght@400;600;700&family=Raleway:wght@600;700&display=swap" rel="stylesheet">
<style>
:root{
  --red:#c4120f;
  --red-dark:#a90e0c;
  --orange:#f9b234;
  --orange-dark:#e39a1a;
  --band:#e6a842;
  --text:#333;
  --muted:#777;
  --light:#f3f3f3;
  --footer:#2b2523;
  --footer-text:#d8d2cf;
  --white:#fff;
}
*{box-sizing:border-box;margin:0;padding:0}
html,body{width:683px;height:1200px;overflow:hidden}
body{font-family:"Open Sans",sans-serif;color:var(--text);background:var(--white);position:relative}
a{color:inherit;text-decoration:none}
.abs{position:absolute}
.heading{font-family:"Raleway",sans-serif;font-weight:700;text-transform:uppercase;letter-spacing:.2px}

/* header */
.site-header{position:absolute;top:0;left:0;width:683px;height:53px;border-top:2px solid var(--red);background:var(--white)}
.brand{position:absolute;left:58px;top:20px;display:flex;align-items:center;gap:6px;color:var(--red);font-size:15px;font-weight:600}
.brand-dot{width:10px;height:10px;border-radius:50%;background:var(--orange)}
.utility{position:absolute;right:58px;top:10px;display:flex;gap:14px;font-size:7.5px;color:#444;align-items:center}
.utility span{display:flex;align-items:center;gap:4px}
.main-nav{position:absolute;right:58px;top:34px;display:flex;gap:16px;font-size:8px;font-weight:600;color:#333}
.main-nav .active{color:var(--orange-dark)}

/* hero */
.hero{position:absolute;top:53px;left:0;width:683px;height:248px;
  background:radial-gradient(ellipse at 50% 65%,#5c6d7a 0%,#8a7e73 38%,#a58d7c 60%,#8d7a6c 100%)}
.hero-title{position:absolute;top:58px;width:100%;text-align:center;font-family:"Raleway",sans-serif;font-weight:700;font-size:37px;color:var(--white);text-shadow:0 1px 3px rgba(0,0,0,.35)}
.hero-sub{position:absolute;top:110px;left:120px;width:443px;text-align:center;font-size:12px;line-height:18px;color:var(--white);text-shadow:0 1px 2px rgba(0,0,0,.5)}
.btn{position:absolute;display:flex;align-items:center;justify-content:center;font-weight:700;text-transform:uppercase;font-size:8px;letter-spacing:.3px;color:var(--white)}
.btn-orange{background:var(--orange);border-bottom:2px solid var(--orange-dark)}
.btn-red{background:var(--red);border:1.5px solid var(--white)}
.arrow{position:absolute;top:116px}

/* sections */
.welcome{position:absolute;top:301px;left:0;width:683px;height:123px;text-align:center}
.section-title{position:absolute;width:100%;text-align:center;font-size:14px;color:#222}
.welcome p{position:absolute;top:50px;left:112px;width:459px;font-size:9.5px;line-height:16px;color:var(--muted)}

.products{position:absolute;top:424px;left:0;width:683px;height:266px;background:var(--light)}
.product-name{position:absolute;left:56px;top:59px;font-size:10.5px;color:#222}
.product-copy{position:absolute;left:56px;top:80px;width:285px;font-size:6.4px;line-height:14.2px;color:#555}
.product-copy p+p{margin-top:14px}
.product-photo{position:absolute;left:361px;top:57px;width:266px;height:176px;border:3px solid var(--white);box-shadow:0 0 0 1px #ddd;
  background:linear-gradient(90deg,#3c6fa8 0 9%,#b07a66 9% 100%)}
.or{position:absolute;left:159px;top:225px;font-size:7.5px;font-weight:700;color:#444}
.more-link{position:absolute;left:181px;top:225px;font-size:7.5px;font-weight:700;color:var(--red)}

.builder{position:absolute;top:690px;left:0;width:683px;height:140px;background:linear-gradient(135deg,#e0a13d,#ecb451 55%,#e3a43f)}
.builder .section-title{top:24px;color:var(--white)}
.builder p{position:absolute;top:46px;width:100%;text-align:center;font-size:8px;line-height:14px;color:#fff5e0}
.location{position:absolute;left:109px;top:88px;width:418px;height:28px;background:var(--white);font-size:7px;color:#444;padding:9px 0 0 12px}
.location .drop{position:absolute;right:0;top:0;width:37px;height:28px;background:linear-gradient(#eee,#ccc);display:flex;align-items:center;justify-content:center}
.go{position:absolute;left:534px;top:88px;width:40px;height:28px;background:var(--red);border-radius:2px;color:var(--white);font-weight:700;font-size:9px;display:flex;align-items:center;justify-content:center}

.howto{position:absolute;top:830px;left:0;width:683px;height:153px}
.howto p{position:absolute;top:55px;left:130px;width:423px;text-align:center;font-size:6.8px;line-height:14px;color:#555}

.newsletter{position:absolute;top:983px;left:0;width:683px;height:49px;background:var(--red);color:var(--white)}
.newsletter .label{position:absolute;left:93px;top:13px;font-size:7.5px;font-weight:600;line-height:12px}
.newsletter .label b{display:block;font-size:11.5px;letter-spacing:.3px}
.newsletter .email{position:absolute;left:198px;top:12px;width:354px;height:22px;background:var(--white);font-size:6px;color:#999;padding:7px 0 0 14px}
.newsletter .subscribe{position:absolute;left:562px;top:10px;width:66px;height:26px;border:1.5px solid var(--white);font-size:8px;font-weight:700;display:flex;align-items:center;justify-content:center}

.site-footer{position:absolute;top:1032px;left:0;width:683px;height:168px;background:var(--footer);color:var(--footer-text)}
.footer-brand{position:absolute;left:53px;top:30px;display:flex;align-items:center;gap:5px;color:var(--white);font-size:11px;font-weight:600}
.footer-brand .brand-dot{background:var(--white)}
.footer-about{position:absolute;left:56px;top:55px;width:130px;font-size:6.4px;line-height:12.8px}
.cards{position:absolute;left:56px;top:101px;display:flex;gap:3px}
.cards span{width:22px;height:13px;border-radius:1px;background:#f0f0f0}
.cards span:nth-child(2){background:#e6e9f2}
.cards span:nth-child(5){background:#2b6cb0}
.col{position:absolute;top:26px}
.col h4{font-family:"Raleway",sans-serif;font-size:8.5px;font-weight:700;color:var(--white);margin-bottom:9px}
.col li{list-style:none;font-size:6.4px;line-height:12.8px}
.col.underline li{text-decoration:underline}
.col.account li{line-height:14px}
.divider{position:absolute;top:22px;width:1px;height:110px;background:#3d3532}
.contact li{display:flex;gap:9px;margin-bottom:10px;line-height:11px}
.contact li+li{margin-top:4px}
.contact svg{flex:none;margin-top:2px}
.copyright{position:absolute;left:57px;top:142px;font-size:6.4px}
.follow{position:absolute;left:508px;top:141px;font-size:6.4px;display:flex;gap:3px;align-items:center}
.follow .sq{width:8px;height:8px;background:var(--white);border-radius:1px}
.follow .lbl{margin-right:6px}
</style>
</head>
<body>

<header class="site-header">
  <a class="brand" href="#"><span class="brand-dot"></span>GnomonVale.com</a>
  <div class="utility">
    <span><svg width="12" height="8" viewBox="0 0 12 8"><circle cx="6" cy="4" r="3.5" fill="none" stroke="#f0a020" stroke-width="1"/><path d="M2.5 4h7M6 .5v7" stroke="#f0a020" stroke-width=".8"/></svg>Language</span>
    <span><svg width="12" height="10" viewBox="0 0 12 10"><path d="M0 1h2l2 6h6l1.5-4.5H3" fill="none" stroke="#f0a020" stroke-width="1.2"/><circle cx="5" cy="9" r="1" fill="#f0a020"/><circle cx="9" cy="9" r="1" fill="#f0a020"/></svg>Cart (0)</span>
  </div>
  <nav class="main-nav">
    <a class="active" href="#">Home</a><a href="#">About Us</a><a href="#">Products</a><a href="#">Shop</a><a href="#">Blog</a><a href="#">News</a><a href="#">Contact Us</a>
    <svg width="8" height="8" viewBox="0 0 8 8"><circle cx="3.3" cy="3.3" r="2.5" fill="none" stroke="#222" stroke-width="1.2"/><path d="M5.2 5.2 7.5 7.5" stroke="#222" stroke-width="1.4"/></svg>
  </nav>
</header>

<section class="hero" role="img" aria-label="Photograph of a large stone sundial set into a plaza, with hour numerals around its dial">
  <h1 class="hero-title">GnomonVale</h1>
  <p class="hero-sub">We can manufacture your Sundial, design to your specific location. Becoming a unique piece considering your location, and wall decliantion.</p>
  <a class="btn btn-orange" href="#" style="left:245px;top:157px;width:81px;height:24px">Buy Sundial</a>
  <a class="btn btn-red" href="#" style="left:347px;top:157px;width:91px;height:24px">Read More</a>
  <svg class="arrow" style="left:38px" width="10" height="16" viewBox="0 0 10 16"><path d="M8 1 2 8l6 7" fill="none" stroke="#fff" stroke-width="1.6"/></svg>
  <svg class="arrow" style="left:635px" width="10" height="16" viewBox="0 0 10 16"><path d="M2 1l6 7-6 7" fill="none" stroke="#fff" stroke-width="1.6"/></svg>
</section>

<section class="welcome">
  <h2 class="section-title heading" style="top:26px">Welcome to GnomonVale</h2>
  <p>Sundials are instruments that tell you the time with the shadow of the sun. To design a sundial you need to know exactly where you are going to put it, i.e. you need to know the longitude, the latitude and the orientation of the wall with respect to North.</p>
</section>

<section class="products">
  <h2 class="section-title heading" style="top:22px">Our Product</h2>
  <h3 class="product-name heading">Wall Sundial</h3>
  <div class="product-copy">
    <p>Sundials are instruments that tell you the time with the shadow of the sun. To design a sundial you need to know exactly where you are going to put it, i.e. you need to know the longitude, the latitude and the orientation of the wall with respect to North.</p>
    <p>I have designed this page and integrated TerraPlot Maps. It helps you to easily find all the parameters needed and finally produces a printable page with a cut-out paper sundial, that can be cut and folded to give you a vertical sundial.This page allows you to make your own Cut Out Paper Vertical Sundial customized to your place on earth and the declination of the wall you are going to put it on.</p>
  </div>
  <a class="btn btn-orange" href="#" style="left:56px;top:216px;width:92px;height:25px">Buy Sundial</a>
  <span class="or">OR</span>
  <a class="more-link" href="#">GET MORE DETAILS &gt;&gt;</a>
  <div class="product-photo" role="img" aria-label="Photograph of a white paper sundial fixed to a brick wall"></div>
</section>

<section class="builder">
  <h2 class="section-title heading">Build Your Customized Sundial</h2>
  <p>Select the location where you want to place your paper sundial, mark a line along building wall where you want to put it.<br>Write your address and press Go! (e.g. Market square, Bristol, UK)</p>
  <div class="location">SELECT YOUR LOCATION :
    <span class="drop"><svg width="8" height="5" viewBox="0 0 8 5"><path d="M0 0h8L4 5z" fill="#666"/></svg></span>
  </div>
  <a class="go" href="#">GO</a>
</section>

<section class="howto">
  <h2 class="section-title heading" style="top:28px">How to Make a Paper Sundial</h2>
  <p>Sed ut perspiciatis unde omnis iste natus error sit voluptatem accusantium doloremque laudantium, totam rem aperiam, eaque ipsa quae ab illo inventore veritatis et quasi architecto beatae vitae dicta sunt explicabo.</p>
  <a class="btn btn-orange" href="#" style="left:270px;top:96px;width:143px;height:28px">Click Here to Read More</a>
</section>

<section class="newsletter">
  <svg class="abs" style="left:55px;top:12px" width="26" height="22" viewBox="0 0 26 22"><g transform="rotate(-12 13 11)"><rect x="2" y="4" width="22" height="15" rx="2" fill="#fff"/><path d="M2 6l11 7 11-7" fill="none" stroke="#c4120f" stroke-width="1.6"/></g></svg>
  <div class="label">NEWSLETTER<b>SUBSCRIPTION</b></div>
  <div class="email">ENTER EMAIL ADDRESS</div>
  <a class="subscribe" href="#">SUBSCRIBE</a>
</section>

<footer class="site-footer">
  <div class="footer-brand"><span class="brand-dot"></span>GnomonVale.com</div>
  <p class="footer-about">At vero eos et accusamus et iusto odio dignissimos ducimus qui blanditiis pra esentium voluptatum delen</p>
  <div class="cards"><span></span><span></span><span></span><span></span><span></span></div>

  <div class="divider" style="left:196px"></div>
  <div class="col underline" style="left:214px"><h4>QUICK LINKS</h4>
    <ul><li>Contact</li><li>FAQ</li><li>Delivery</li><li>Returns</li><li>Track Orders</li><li>Subscribe</li></ul></div>
  <div class="divider" style="left:300px"></div>
  <div class="col" style="left:320px"><h4>EXTRAS</h4>
    <ul><li>Specials</li><li>New products</li><li>Top sellers</li><li>Our stores</li><li>Contact us</li><li>About us</li></ul></div>
  <div class="divider" style="left:398px"></div>
  <div class="col account" style="left:413px"><h4>MY ACCOUNT</h4>
    <ul><li>Delivery Information</li><li>Privacy Policy</li><li>Returns Policy</li><li>Terms and Conditions</li><li>FAQs</li></ul></div>
  <div class="divider" style="left:505px"></div>
  <div class="col contact" style="left:535px"><h4>CONTACT US</h4>
    <ul>
      <li><svg width="5" height="7" viewBox="0 0 5 7"><path d="M2.5 7 .3 3.2A2.5 2.5 0 1 1 4.7 3.2z" fill="#fff"/></svg><span>210 Harbor Lane<br>Oakland, CA 94607</span></li>
      <li><svg width="6" height="6" viewBox="0 0 6 6"><path d="M1 0h1.3l.6 1.6-.8.6a4 4 0 0 0 1.7 1.7l.6-.8L6 3.7V5c0 .5-.5 1-1 1A5 5 0 0 1 0 1c0-.5.5-1 1-1z" fill="#fff"/></svg><span>1 555 010 020</span></li>
      <li><svg width="6" height="5" viewBox="0 0 6 5"><rect width="6" height="5" fill="#fff"/><path d="M0 .5l3 2 3-2" fill="none" stroke="#2b2523" stroke-width=".7"/></svg><span style="text-decoration:underline">info@gnomonvale.com</span></li>
    </ul></div>

  <p class="copyright">Copyrights © 2016, GnomonVale. All Rights Reserved</p>
  <div class="follow"><span class="lbl">Follow us on :</span><span class="sq"></span><span class="sq"></span><span class="sq"></span><span class="sq"></span><span class="sq"></span><span class="sq"></span></div>
</footer>

</body>
</html>
```